KR Appraisals website redesign

I would like to refresh my existing website of www.krappraisals-example.com with new graphics, look and feel, as well as updated structure and wording. Content and layout changes have been uploaded to this project Brief.

My existing website has a dark feel. I am now looking for a light and energetic feel. Financial Services is my industry, so the website should be reflect that. I would also like to reflect the concepts of Trust, Service and Expertise.

The website must be serious and upmarket.

Target Market(s)

Corporate board members, CFO's, treasurers and controllers
Auditors, tax advisors, private equity and venture capital asset managers, investors, tax authorities

Industry/Entity Type

Financial Service

Coding

Coded - Design and coding required

Number of Pages Required

5+ page

Font styles to use
Sans Serif
Other font styles liked:
• Designer can choose another modern font

Colors
0355a3
3277b5
85acd3
eaf1f7
f37122
f68d4d
9bcb3c
acd037
cadf82

Requirements
Must have
• Good hi resolution pictures that convey "Finance", "Trust", "Service" or "Expertise".
• An anti-bot (such as Captcha) mechanism in the contact form.
Should not have
• Must not have all content on one rolling screen.

```html
<!DOCTYPE html>
<html lang="en">
<head>
<meta charset="utf-8">
<title>KR Appraisals – Services</title>
<link href="https://fonts.googleapis.com/css2?family=Montserrat:wght@400;500;600&family=Nunito+Sans:wght@400;600&display=swap" rel="stylesheet">
<style>
  :root {
    --blue: #0355a3;
    --orange: #f37122;
    --green: #9bcb3c;
    --grey-text: #6b6b6b;
    --nav-grey: #7a7a7a;
    --panel: #f2f2f2;
    --footer: #333333;
    --footer-text: #a8a8a8;
    --footer-rule: #5a5a5a;
    --white: #ffffff;
  }
  * { margin: 0; padding: 0; box-sizing: border-box; }
  html, body { width: 1200px; height: 1144px; overflow: hidden; background: var(--white); }
  body { position: relative; font-family: "Montserrat", sans-serif; }

  .site-header {
    position: absolute; left: 0; top: 0; width: 1200px; height: 100px;
    background: linear-gradient(90deg, #e6e6dc 0%, #ecece0 45%, #f4f4e2 100%);
  }
  .brand {
    position: absolute; left: 161px; top: 30px; height: 40px; padding: 0 8px;
    display: flex; align-items: center; gap: 8px;
    font-family: "Montserrat", sans-serif; font-weight: 400; font-size: 20px;
    color: #7d7d7d; letter-spacing: 0.5px;
  }
  .brand-mark { width: 12px; height: 12px; background: #7d7d7d; }
  .main-nav {
    position: absolute; top: 45px; right: 161px; display: flex; gap: 40px;
    font-size: 11.5px; font-weight: 500; color: var(--nav-grey); text-transform: uppercase;
  }
  .main-nav .active { color: var(--blue); }

  .page-title {
    position: absolute; top: 186px; left: 0; width: 1200px; text-align: center;
    color: var(--orange); font-size: 38px; font-weight: 600; letter-spacing: -0.5px;
  }

  .service-panel {
    position: absolute; left: 562px; top: 281px; width: 477px; height: 420px;
    background: var(--panel);
  }
  .service-photo {
    position: absolute; left: 161px; top: 341px; width: 439px; height: 293px;
    background: linear-gradient(120deg, #c9b9a0 0%, #d6dbe0 40%, #8c8f96 70%, #2a3140 100%);
  }
  .service-title {
    position: absolute; left: 639px; top: 393px;
    color: var(--green); font-size: 29px; font-weight: 600; letter-spacing: -0.3px;
  }
  .service-text {
    position: absolute; left: 639px; top: 453px; width: 370px;
    font-family: "Nunito Sans", sans-serif; font-size: 10.6px; line-height: 19px;
    color: var(--grey-text);
  }

  .site-footer { position: absolute; left: 0; top: 791px; width: 1200px; height: 353px; }
  .footer-shape { position: absolute; left: 0; top: 0; }
  .footer-brand {
    position: absolute; top: 75px; left: 0; width: 1200px; text-align: center;
    font-size: 22px; font-weight: 400; color: #8a8a8a; letter-spacing: 0.5px;
  }
  .footer-nav {
    position: absolute; left: 161px; top: 145px; width: 878px; height: 45px;
    border-top: 1px solid var(--footer-rule); border-bottom: 1px solid var(--footer-rule);
    display: flex; justify-content: center; align-items: center; gap: 40px;
    font-size: 11px; font-weight: 500; color: #9a9a9a; text-transform: uppercase;
  }
  .footer-nav .active { color: var(--green); }
  .footer-col { position: absolute; top: 218px; font-family: "Nunito Sans", sans-serif; font-size: 10.5px; color: var(--footer-text); }
  .footer-col h3 { font-family: "Montserrat", sans-serif; color: var(--orange); font-size: 13px; font-weight: 600; margin-bottom: 12px; }
  .credits p { line-height: 22.5px; }
  .credits .hl { color: var(--green); }
  .credits .wt { color: var(--white); }
  .contact-line { display: flex; align-items: flex-start; gap: 8px; padding-left: 2px; }
  .contact-line p { line-height: 16.5px; }
  .phone { margin-top: 13px; color: var(--white); font-size: 11.5px; font-weight: 600; align-items: center; }
  .badge { position: absolute; left: 855px; background: #4a4a4a; }
  .badge-one { top: 209px; width: 170px; height: 40px; border-radius: 4px; }
  .badge-two { top: 258px; width: 170px; height: 70px; border-radius: 4px; }
</style>
</head>
<body>
  <header class="site-header">
    <div class="brand"><span class="brand-mark"></span>KR APPRAISALS</div>
    <nav class="main-nav">
      <span>Home</span><span>About</span><span class="active">Services</span><span>News &amp; Views</span><span>Contact</span>
    </nav>
  </header>

  <h1 class="page-title">OUR SERVICES</h1>

  <div class="service-panel"></div>
  <div class="service-photo" role="img" aria-label="Business team in a bright office shaking hands at a meeting table"></div>
  <h2 class="service-title">M&amp;A ADVISORY</h2>
  <p class="service-text">Through our international network of M&amp;A professionals, KR Appraisals can assist companies with buying other companies or selling (parts of) their companies. KR Appraisals offers a flexible approach, assisting companies with part of the process or providing a full-service approach.</p>

  <footer class="site-footer">
    <svg class="footer-shape" width="1200" height="353" viewBox="0 0 1200 353">
      <polygon points="0,68 600,0 1200,68 1200,353 0,353" fill="#333333"/>
    </svg>
    <div class="footer-brand">KR APPRAISALS</div>
    <nav class="footer-nav">
      <span class="active">Home</span><span>About</span><span>Services</span><span>News &amp; Views</span><span>Contact</span>
    </nav>

    <div class="footer-col credits" style="left:163px">
      <h3>CREDITS</h3>
      <p>© 2019 <span class="hl">KR Appraisals</span></p>
      <p>Logo by <span class="wt">Mara Jensen</span></p>
      <p>Website by <span class="hl">Northline Webworks</span></p>
    </div>

    <div class="footer-col" style="left:390px">
      <h3>LEIDEN</h3>
      <div class="contact-line">
        <svg width="9" height="12" viewBox="0 0 9 12"><path d="M4.5 0C2 0 0 2 0 4.4 0 7.6 4.5 12 4.5 12S9 7.6 9 4.4C9 2 7 0 4.5 0zm0 6.2a1.8 1.8 0 1 1 0-3.6 1.8 1.8 0 0 1 0 3.6z" fill="#9bcb3c"/></svg>
        <p>Kanaalweg 48<br>2311 AB Leiden</p>
      </div>
      <div class="contact-line phone">
        <svg width="12" height="12" viewBox="0 0 12 12"><path d="M2.4 0.5l2 2.3-1 1.4c.7 1.6 1.9 2.8 3.4 3.5l1.4-1 2.3 2-1 2.3C5.6 11 1 6.4 0 1.5z" fill="#9bcb3c"/></svg>
        <span>070 555 0148</span>
      </div>
    </div>

    <div class="footer-col" style="left:617px">
      <h3>AMSTERDAM</h3>
      <div class="contact-line">
        <svg width="9" height="12" viewBox="0 0 9 12"><path d="M4.5 0C2 0 0 2 0 4.4 0 7.6 4.5 12 4.5 12S9 7.6 9 4.4C9 2 7 0 4.5 0zm0 6.2a1.8 1.8 0 1 1 0-3.6 1.8 1.8 0 0 1 0 3.6z" fill="#9bcb3c"/></svg>
        <p>Zuidplein 17<br>1077 XV Amsterdam</p>
      </div>
      <div class="contact-line phone">
        <svg width="12" height="12" viewBox="0 0 12 12"><path d="M2.4 0.5l2 2.3-1 1.4c.7 1.6 1.9 2.8 3.4 3.5l1.4-1 2.3 2-1 2.3C5.6 11 1 6.4 0 1.5z" fill="#9bcb3c"/></svg>
        <span>020 555 0192</span>
      </div>
    </div>

    <div class="badge badge-one" role="img" aria-label="Professional membership badge"></div>
    <div class="badge badge-two" role="img" aria-label="Appraisal society accreditation badge"></div>
  </footer>
</body>
</html>
```